Upmarket Dessert Lounge needs a Business Card Design

We are an upmarket dessert lounge needing a business card to match our image.

We want something that is simple yet beautiful, feminine, classy, sophisticated and elegant. We want it to stand out and don't mind if it is bold.

The design should include our logo and colours of red or maroon with gold highlights. We don't mind if black is used.

Marlow & Quince

Target Market(s)

For those who like to indulge or treat themselves and give in to their temptations on good quality desserts.

Industry/Entity Type

Business

Requirements
Must have
• Must include our logo and our name

Marlow & Quince

M & Q

```html
<!DOCTYPE html>
<html lang="en">
<head>
<meta charset="utf-8">
<title>Marlow &amp; Quince — Business Card</title>
<link rel="stylesheet" href="https://fonts.googleapis.com/css2?family=Cormorant+Garamond:wght@500&family=Libre+Baskerville:wght@700&family=Open+Sans:wght@400&display=swap">
<style>
  :root {
    --backdrop: #ece6df;
    --maroon: #7a1517;
    --cream: #f6d7a7;
    --card-white: #ffffff;
    --text-light: #ffffff;
    --shadow: rgba(40, 20, 10, 0.28);
  }
  * { box-sizing: border-box; margin: 0; padding: 0; }
  html, body {
    width: 1200px;
    height: 758px;
    overflow: hidden;
    background: var(--backdrop);
  }
  .canvas {
    position: relative;
    width: 1200px;
    height: 758px;
  }
  .card {
    position: absolute;
    width: 540px;
    height: 310px;
    border-radius: 30px;
    overflow: hidden;
    box-shadow: 0 10px 26px var(--shadow);
  }

  /* Front card */
  .card-front {
    left: 50px;
    top: 160px;
    display: flex;
    background: var(--card-white);
  }
  .front-brand {
    width: 262px;
    flex: none;
    padding: 0 24px;
    display: flex;
    align-items: center;
    justify-content: center;
  }
  .brand-name {
    font-family: "Cormorant Garamond", serif;
    font-weight: 500;
    font-size: 23px;
    letter-spacing: 1px;
    white-space: nowrap;
    text-align: center;
    color: var(--maroon);
    text-transform: uppercase;
  }
  .front-divider {
    width: 4px;
    flex: none;
    background: var(--cream);
  }
  .front-details {
    flex: 1;
    background: var(--maroon);
    color: var(--text-light);
    padding: 40px 0 0 52px;
    font-family: "Open Sans", sans-serif;
  }
  .person-name {
    font-family: "Libre Baskerville", serif;
    font-weight: 700;
    font-size: 17px;
    letter-spacing: 0.5px;
  }
  .person-title {
    font-size: 13px;
    margin: 4px 0 14px;
  }
  .contact-list { list-style: none; }
  .contact-list li {
    display: flex;
    align-items: center;
    gap: 6px;
    font-size: 13px;
    line-height: 18px;
    white-space: nowrap;
  }
  .contact-list svg { width: 11px; height: 11px; fill: var(--text-light); flex: none; }
  .address {
    margin-top: 18px;
    font-size: 13px;
    line-height: 19px;
  }

  /* Back card */
  .card-back {
    left: 612px;
    top: 290px;
    background: var(--maroon);
    display: flex;
    flex-direction: column;
    align-items: center;
  }
  .monogram {
    margin-top: 70px;
    font-family: "Cormorant Garamond", serif;
    font-weight: 500;
    font-size: 84px;
    line-height: 1;
    color: var(--cream);
  }
  .web-address {
    margin-top: 60px;
    font-family: "Open Sans", sans-serif;
    font-size: 19px;
    letter-spacing: 2.5px;
    color: var(--text-light);
  }
</style>
</head>
<body>
<main class="canvas">

  <section class="card card-front" aria-label="Business card front">
    <div class="front-brand">
      <span class="brand-name">Marlow &amp; Quince</span>
    </div>
    <div class="front-divider"></div>
    <div class="front-details">
      <p class="person-name">Your name</p>
      <p class="person-title">Title</p>
      <ul class="contact-list">
        <li>
          <svg viewBox="0 0 24 24" aria-hidden="true"><path d="M6.6 10.8a15 15 0 0 0 6.6 6.6l2.2-2.2c.3-.3.7-.4 1-.2 1.1.4 2.3.6 3.6.6.6 0 1 .4 1 1V20c0 .6-.4 1-1 1A17 17 0 0 1 3 4c0-.6.4-1 1-1h3.5c.6 0 1 .4 1 1 0 1.3.2 2.5.6 3.6.1.3 0 .7-.2 1z"/></svg>
          987-654-3210
        </li>
        <li>
          <svg viewBox="0 0 24 24" aria-hidden="true"><path d="M7 1h10c1.1 0 2 .9 2 2v18c0 1.1-.9 2-2 2H7c-1.1 0-2-.9-2-2V3c0-1.1.9-2 2-2zm0 4v12h10V5z"/></svg>
          987-654-3210
        </li>
        <li>
          <svg viewBox="0 0 24 24" aria-hidden="true"><path d="M2 5h20v14H2zm2 2v.5l8 5 8-5V7z"/></svg>
          info@marlowquince.com
        </li>
        <li>
          <svg viewBox="0 0 24 24" aria-hidden="true"><path d="M12 2a10 10 0 1 0 0 20 10 10 0 0 0 0-20zm0 2c1 0 2.2 2 2.7 5H9.3C9.8 6 11 4 12 4zM4.3 11h3c0 .7 0 1.4.1 2h-3a8 8 0 0 1 0-2zm12.4 0h3a8 8 0 0 1 0 2h-3c.1-.6.1-1.3 0-2zm-7.4 0h5.4a16 16 0 0 1 0 2H9.3a16 16 0 0 1 0-2zm0 4h5.4c-.5 3-1.7 5-2.7 5s-2.2-2-2.7-5z"/></svg>
          www.marlowquince.com
        </li>
      </ul>
      <p class="address">Street Name, City Name<br>State Zip Code</p>
    </div>
  </section>

  <section class="card card-back" aria-label="Business card back">
    <p class="monogram">M&amp;Q</p>
    <p class="web-address">www.marlowquince.com</p>
  </section>

</main>
</body>
</html>
```